Tevlora website

Web design for small consulting firm
It can be simple, easy to find approach

The primary use is business to business for

a. people wanting to find out a bit more of us after receiving a business card
b. Search words to draw people from search engines to us

Target Market(s)

Senior staff of large companies, in their work capacity
MD / CEO / CFO , directors, etc.

Industry/Entity Type

Business

Colors
ffffff
f79020
faa54b
33a6d7

```html
<!DOCTYPE html>
<html lang="en">
<head>
<meta charset="utf-8">
<title>Tevlora</title>
<link rel="stylesheet" href="https://fonts.googleapis.com/css2?family=Open+Sans:ital,wght@0,300;0,400;0,600;0,700;1,400&display=swap">
<style>
:root{
  --white:#ffffff;
  --orange:#f79020;
  --orange-soft:#faa54b;
  --sky:#33a6d7;
  --blue:#0a72b8;
  --link:#1360a8;
  --ink:#333333;
  --body:#4a4a4a;
  --muted:#777777;
  --page:#fafbfb;
  --footer:#e2e2e2;
  --rule:#c9c9c9;
}
*{margin:0;padding:0;box-sizing:border-box}
html,body{width:1024px;height:1200px;overflow:hidden}
body{position:relative;background:var(--page);font-family:"Open Sans",Arial,sans-serif;color:var(--ink)}
.abs{position:absolute}

.site-header{position:absolute;left:0;top:0;width:1024px;height:75px;background:var(--white)}
.brand{left:136px;top:17px;font-size:34px;font-weight:700;color:var(--blue);letter-spacing:-.5px;line-height:1.1}
.social{display:flex;gap:7px}
.social span{width:20px;height:20px;border-radius:50%;background:var(--blue)}
.social span:nth-child(2){background:var(--sky)}
.header-social{left:809px;top:16px}
.call{left:664px;top:41px;display:flex;align-items:center;gap:6px;font-size:13.5px;font-weight:600;color:var(--muted);letter-spacing:.3px}
.call .icon{width:18px;height:18px;border-radius:3px;background:var(--orange);display:flex;align-items:center;justify-content:center}
.call b{color:var(--orange);font-weight:600}

.main-nav{position:absolute;left:0;top:75px;width:1024px;height:41px;background:var(--blue);display:flex;align-items:center;padding-left:142px;padding-right:137px;justify-content:space-between}
.main-nav a{color:var(--white);text-decoration:none;font-size:13.5px;font-weight:700;letter-spacing:2px}

.hero{position:absolute;left:0;top:116px;width:1024px;height:378px;background:linear-gradient(90deg,#c9d6e2 0%,#e7edf2 40%,#f2f4f6 70%,#dfe6ec 100%)}
.hero-panel{left:0;top:302px;width:534px;height:150px;background:rgba(241,130,18,.88);padding:18px 0 0 136px;color:var(--white)}
.hero-panel h1{font-size:25.5px;font-weight:700;letter-spacing:.6px;margin-bottom:12px}
.hero-panel p{font-size:15px;font-weight:300;line-height:20px;width:350px}

.section-title{font-size:20px;font-weight:400;color:var(--ink)}
.dotted{height:4px;border-top:1px dotted var(--rule);border-bottom:1px dotted var(--rule)}
.feature{top:536px;width:238px}
.feature .section-title{margin-left:2px;height:38px}
.feature .photo{margin-top:10px;width:238px;height:109px;border-radius:2px}
.feature p{margin-top:17px;font-size:9.6px;line-height:14.4px;color:var(--body)}
.feature a{display:inline-block;margin-top:10px;font-size:10px;font-weight:700;color:var(--link)}

.clients{left:136px;top:836px;width:480px}
.clients .section-title{margin-left:3px;height:40px}
.client-row{display:flex;justify-content:space-between;align-items:center;margin-top:16px;height:52px}
.client-row span{font-size:14px;font-weight:700;color:#a3a3a3;letter-spacing:.3px;display:flex;align-items:center;gap:6px}
.client-row i{width:12px;height:12px;background:#a3a3a3;border-radius:50%}
.quote{left:134px;top:972px;width:490px;font-size:13.6px;font-style:italic;line-height:20px;color:var(--body)}
.quote-by{left:134px;top:1067px;font-size:10px;font-weight:700;color:var(--link)}

.news{left:649px;top:836px;width:239px}
.news .section-title{height:40px;display:flex;align-items:flex-start;gap:9px}
.news .section-title svg{margin-top:6px}
.news article{margin-top:6px;position:relative;height:94px}
.news h3{font-size:12px;font-weight:600;color:var(--ink);margin-left:1px}
.news .thumb{position:absolute;left:-2px;top:20px;width:68px;height:58px}
.news p{position:absolute;left:80px;top:20px;width:160px;font-size:9.6px;line-height:14.4px;color:var(--muted)}
.news time{position:absolute;left:80px;top:67px;font-size:7.6px;font-weight:700;color:var(--muted)}

.site-footer{position:absolute;left:0;top:1116px;width:1024px;height:84px;background:var(--footer)}
.footer-links{left:138px;top:26px;font-size:10px;font-weight:700;color:var(--ink);letter-spacing:.6px;word-spacing:3px}
.copy{left:137px;top:50px;font-size:9.6px;color:var(--ink)}
.footer-social{left:396px;top:24px;gap:11px}
.footer-social span{width:21px;height:21px}
.contact{left:745px;font-size:9.6px;color:var(--ink);display:flex;align-items:center;gap:12px}
</style>
</head>
<body>

<header class="site-header">
  <div class="abs brand">Tevlora</div>
  <div class="abs social header-social" aria-label="Social links"><span></span><span></span><span></span></div>
  <div class="abs call">
    <span class="icon"><svg width="11" height="11" viewBox="0 0 24 24"><path fill="#fff" d="M6.6 10.8a15 15 0 006.6 6.6l2.2-2.2c.3-.3.7-.4 1-.2 1.1.4 2.3.6 3.6.6.6 0 1 .4 1 1V20c0 .6-.4 1-1 1A17 17 0 013 4c0-.6.4-1 1-1h3.5c.6 0 1 .4 1 1 0 1.3.2 2.5.6 3.6.1.3 0 .7-.2 1z"/></svg></span>
    CALL US TODAY <b>+1800.555.0142</b>
  </div>
</header>

<nav class="main-nav">
  <a href="#">HOME</a><a href="#">SERVICES</a><a href="#">BLOG</a><a href="#">ABOUT</a><a href="#">CLIENTS</a><a href="#">CONTACT</a>
</nav>

<section class="hero" role="img" aria-label="Photo of three business colleagues talking in a bright office"></section>
<div class="abs hero-panel">
  <h1>We Bring Businesses Forward</h1>
  <p>It is a long established fact that a reader will be distracted by the readable content of a page when looking at its layout.</p>
</div>

<div class="abs feature" style="left:136px">
  <h2 class="section-title">Who We Are</h2>
  <div class="dotted"></div>
  <div class="photo" role="img" aria-label="Photo of a team meeting" style="background:linear-gradient(135deg,#8a8f98,#3b3f46)"></div>
  <p>Lorem ipsum dolor sit amet, consectetur adipisicing elit, sed do eiusmod tempor incididunt ut labore et dolore magna aliqua. Ut enim ad minim veniam, quis nostrud exercitation.</p>
  <a href="#">READ MORE</a>
</div>
<div class="abs feature" style="left:391px">
  <h2 class="section-title">Our Values</h2>
  <div class="dotted"></div>
  <div class="photo" role="img" aria-label="Photo of two business partners" style="background:linear-gradient(135deg,#c9d2da,#4d5763)"></div>
  <p>Lorem ipsum dolor sit amet, consectetur adipisicing elit, sed do eiusmod tempor incididunt ut labore et dolore magna aliqua. Ut enim ad minim veniam, quis nostrud exercitation.</p>
  <a href="#">READ MORE</a>
</div>
<div class="abs feature" style="left:649px">
  <h2 class="section-title">What We Do</h2>
  <div class="dotted"></div>
  <div class="photo" role="img" aria-label="Photo of consultants reviewing documents at a desk" style="background:linear-gradient(135deg,#dfe8f0,#7d8fa3)"></div>
  <p>Lorem ipsum dolor sit amet, consectetur adipisicing elit, sed do eiusmod tempor incididunt ut labore et dolore magna aliqua. Ut enim ad minim veniam, quis nostrud exercitation.</p>
  <a href="#">READ MORE</a>
</div>

<section class="abs clients">
  <h2 class="section-title">Our Clients</h2>
  <div class="dotted"></div>
  <div class="client-row">
    <span><i></i>NORVANE</span><span>Hueline</span><span>Brightwick</span><span>Calderon</span>
  </div>
</section>
<blockquote class="abs quote">“Lorem ipsum dolor sit amet, consectetur adipisicing elit, sed do eiusmod tempor incididunt ut labore et dolore magna aliqua. Ut enim ad minim veniam, quis nostrud exercitation. Lorem ipsum dolor sit amet, consectetur adipisicing elit, sed do eiusmod tempor incididunt ut labore et dolore magna aliqua.”</blockquote>
<div class="abs quote-by">JOHN DOE, Company Inc.</div>

<section class="abs news">
  <h2 class="section-title">
    <svg width="16" height="16" viewBox="0 0 16 16"><rect x="1" y="2.5" width="14" height="12.5" fill="none" stroke="#666" stroke-width="1.4"/><rect x="1" y="2.5" width="14" height="3" fill="#666"/><rect x="4" y="0.5" width="1.6" height="3.5" fill="#666"/><rect x="10.4" y="0.5" width="1.6" height="3.5" fill="#666"/></svg>
    Latest News
  </h2>
  <div class="dotted"></div>
  <article>
    <h3>There are many variations of passages</h3>
    <div class="thumb" role="img" aria-label="Photo of colleagues in an office" style="background:linear-gradient(135deg,#e9edf1,#6c7a88)"></div>
    <p>The point of using Lorem Ipsum is that it has a more-or-less normal distribution of letters, as opposed..</p>
    <time>▫ 8 December 2013</time>
  </article>
  <article>
    <h3>All the Lorem Ipsum generators</h3>
    <div class="thumb" role="img" aria-label="Photo of a businessman signing papers" style="background:linear-gradient(135deg,#d3d9df,#3e4650)"></div>
    <p>The point of using Lorem Ipsum is that it has a more-or-less normal distribution of letters, as opposed..</p>
    <time>▫ 8 December 2013</time>
  </article>
</section>

<footer class="site-footer">
  <div class="abs footer-links">LINKS &nbsp;| &nbsp;LINKS &nbsp;| &nbsp;LINKS &nbsp;| &nbsp;LINKS</div>
  <div class="abs copy">Copyright © 2014. All rights reserved. &nbsp;Company Name</div>
  <div class="abs social footer-social" aria-label="Social links"><span></span><span></span><span></span></div>
  <div class="abs contact" style="top:22px">
    <svg width="16" height="12" viewBox="0 0 16 12"><rect width="16" height="12" rx="1" fill="#777"/><path d="M1 1l7 6 7-6" fill="none" stroke="#e2e2e2" stroke-width="1.3"/></svg>
    info@yourwebsite.com
  </div>
  <div class="abs contact" style="top:46px">
    <svg width="14" height="14" viewBox="0 0 24 24"><path fill="#777" d="M6.6 10.8a15 15 0 006.6 6.6l2.2-2.2c.3-.3.7-.4 1-.2 1.1.4 2.3.6 3.6.6.6 0 1 .4 1 1V20c0 .6-.4 1-1 1A17 17 0 013 4c0-.6.4-1 1-1h3.5c.6 0 1 .4 1 1 0 1.3.2 2.5.6 3.6.1.3 0 .7-.2 1z"/></svg>
    890-55510-20418
  </div>
</footer>

</body>
</html>
```